I need a business card design for a real estate finance, development and management business. We deal with high net worth clients and ask that the business card be neat, clean and sophisticated. We like the attached logo design, font and color and want to incorporate all this into the business card.

Industry/Entity Type

Real Estate

```html
<!DOCTYPE html>
<html lang="en">
<head>
<meta charset="utf-8">
<title>Heron Bay – Business Card</title>
<link rel="stylesheet" href="https://fonts.googleapis.com/css2?family=Open+Sans:wght@400;600;700&display=swap">
<style>
  :root {
    --brand-blue: #1f5d9c;
    --card-white: #ffffff;
    --backdrop: #e4e4e4;
    --ink: #1f5d9c;
  }
  * { box-sizing: border-box; margin: 0; padding: 0; }
  html, body {
    width: 1200px; height: 947px; overflow: hidden;
    background: var(--backdrop);
    font-family: "Open Sans", Arial, sans-serif;
    color: var(--ink);
  }
  .stage {
    width: 1200px; height: 947px;
    display: flex; align-items: center; justify-content: center; gap: 60px;
  }
  .card {
    position: relative;
    width: 520px; height: 300px;
    background: var(--card-white);
    overflow: hidden;
  }
  .card::before, .card::after {
    content: ""; position: absolute; left: 0; right: 0; height: 16px;
    background: var(--brand-blue);
  }
  .card::before { top: 0; }
  .card::after { bottom: 0; }

  .brand-name {
    font-weight: 600;
    text-transform: uppercase;
    letter-spacing: 3px;
    color: var(--ink);
    white-space: nowrap;
  }

  /* front */
  .card-front .brand-name {
    position: absolute; left: 200px; top: 78px;
    font-size: 30px;
  }
  .card-front .divider {
    position: absolute; left: 0; right: 0; top: 138px;
    height: 1.5px; background: var(--brand-blue);
  }
  .contact-line {
    position: absolute; display: flex; gap: 8px;
    font-size: 13px; line-height: 1.35;
    white-space: nowrap;
  }
  .contact-line svg { flex: none; width: 16px; height: 16px; fill: var(--brand-blue); }
  .mobile { left: 22px; top: 58px; align-items: center; }
  .address { left: 22px; top: 156px; }
  .phones { left: 212px; top: 156px; }
  .web { left: 330px; top: 200px; }
  .person-name {
    position: absolute; right: 22px; top: 156px;
    font-size: 17px; letter-spacing: 0.5px;
  }
  .person-name strong { font-weight: 700; }

  /* back */
  .card-back .brand-name {
    position: absolute; left: 0; right: 0; top: 128px;
    text-align: center; font-size: 38px;
  }
</style>
</head>
<body>
<main class="stage">

  <section class="card card-front" aria-label="Business card front">
    <div class="brand-name">Heron Bay</div>

    <div class="contact-line mobile">
      <svg viewBox="0 0 16 16" aria-hidden="true"><path d="M4 1h8a1 1 0 0 1 1 1v12a1 1 0 0 1-1 1H4a1 1 0 0 1-1-1V2a1 1 0 0 1 1-1zm1 2v9h6V3zm3 10.2a.8.8 0 1 0 0-.01z"/></svg>
      <span>+0000 1234 5679</span>
    </div>

    <div class="divider"></div>

    <div class="contact-line address">
      <svg viewBox="0 0 16 16" aria-hidden="true"><path d="M8 1 1 7.5h2V15h4v-4h2v4h4V7.5h2z"/></svg>
      <span>Your Local or business<br>address.</span>
    </div>

    <div class="contact-line phones">
      <svg viewBox="0 0 16 16" aria-hidden="true"><path d="M2 5c0-2 3-3 6-3s6 1 6 3v1h-3V5H5v1H2zm2 2h8l2 7H2zm4 1.5a2 2 0 1 0 0 4 2 2 0 0 0 0-4z"/></svg>
      <span>+000 1234 5679<br>+000 1234 5679</span>
    </div>

    <div class="contact-line web">
      <svg viewBox="0 0 16 16" aria-hidden="true"><path d="M1 2h14v9H1zm5 10h4v1.5h2V15H4v-1.5h2z"/></svg>
      <span>name@yourwebsite.com<br>www.yourwebsite.com</span>
    </div>

    <div class="person-name">YOUR<strong>NAME</strong></div>
  </section>

  <section class="card card-back" aria-label="Business card back">
    <div class="brand-name">Heron Bay</div>
  </section>

</main>
</body>
</html>
```